Automotive Accessories Business Card

Design a business template that match our new logo design and our industry.

https://www.qelmotorgear.com/

Target Market(s)

Aftermarket auto parts and accessories

Industry/Entity Type

automotive

Contact Information for Business Card

company logo

Font styles to use
Serif
Sans Serif

Colors
EB3D1F
EC4F4E
F09395
F8D3D4
FCEDEE

```html
<!DOCTYPE html>
<html lang="en">
<head>
<meta charset="utf-8">
<title>QEL Motor Gear – Business Card</title>
<link rel="stylesheet" href="https://fonts.googleapis.com/css2?family=Arimo:wght@400;700&display=swap">
<style>
  :root {
    --stage: #e9e7e4;
    --card-dark: #3a3a3c;
    --card-dark-text: #5c5c5f;
    --paper: #ffffff;
    --brand-red: #c8202c;
    --ink-dark: #3b3b3d;
    --on-red: #ffffff;
  }
  * { box-sizing: border-box; margin: 0; padding: 0; }
  html, body {
    width: 1200px; height: 768px; overflow: hidden;
    background: var(--stage);
    font-family: "Arimo", Arial, sans-serif;
  }
  .stage { position: relative; width: 1200px; height: 768px; }
  .card {
    position: absolute; top: 230px;
    width: 540px; height: 309px;
    box-shadow: 0 8px 24px rgba(0,0,0,.18);
    overflow: hidden;
  }
  /* Back */
  .card--back { left: 40px; background: var(--card-dark); }
  .card--back .wordmark {
    position: absolute; left: 0; right: 0; top: 112px;
    text-align: center; font-weight: 700; font-size: 40px;
    letter-spacing: 2px; color: var(--card-dark-text);
  }
  .card--back .web {
    position: absolute; left: 0; right: 0; bottom: 48px;
    text-align: center; font-size: 13px; letter-spacing: 4px; color: #d8d8d8;
  }
  /* Front */
  .card--front { left: 620px; background: var(--paper); }
  .card--front .wordmark {
    position: absolute; left: 175px; top: 52px;
    font-weight: 700; font-size: 34px; letter-spacing: 1px; color: var(--brand-red);
  }
  .card--front .band {
    position: absolute; left: 0; top: 120px; width: 400px; height: 16px;
    background: var(--ink-dark);
  }
  .card--front .red-field {
    position: absolute; left: 0; right: 0; top: 136px; bottom: 0;
    background: var(--brand-red); color: var(--on-red);
    display: flex; padding: 28px 22px 0;
  }
  .col { font-size: 12.5px; line-height: 1.35; }
  .col--person { width: 190px; }
  .col--us, .col--ca { padding-left: 16px; border-left: 1px solid rgba(255,255,255,.7); height: 92px; margin-top: 14px; }
  .col--us { width: 152px; margin-right: 14px; }
  .col--ca { width: 160px; }
  .name { font-weight: 700; font-size: 17px; letter-spacing: .5px; margin-bottom: 2px; }
  .phone { display: flex; align-items: center; gap: 6px; margin-top: 4px; }
  .phone svg { width: 11px; height: 11px; fill: var(--on-red); }
</style>
</head>
<body>
<main class="stage">
  <section class="card card--back" aria-label="Card back">
    <div class="wordmark">QEL MOTOR GEAR</div>
    <div class="web">www.qelmotorgear.com</div>
  </section>

  <section class="card card--front" aria-label="Card front">
    <div class="wordmark">QEL MOTOR GEAR</div>
    <div class="band"></div>
    <div class="red-field">
      <div class="col col--person">
        <div class="name">DANIEL MORROW</div>
        <div>Managing Director</div>
        <div>sales@qelmotorgear.com</div>
        <div>www.qelmotorgear.com</div>
      </div>
      <div class="col col--us">
        <div>412 W. Harbor St. Unit C</div>
        <div>Riverside, CA, 92501</div>
        <div>United States</div>
        <div class="phone"><svg viewBox="0 0 24 24"><path d="M6.6 10.8a15.1 15.1 0 0 0 6.6 6.6l2.2-2.2a1 1 0 0 1 1-.25 11.4 11.4 0 0 0 3.6.57 1 1 0 0 1 1 1V20a1 1 0 0 1-1 1A17 17 0 0 1 3 4a1 1 0 0 1 1-1h3.5a1 1 0 0 1 1 1c0 1.25.2 2.45.57 3.57a1 1 0 0 1-.25 1z"/></svg>1-866-555-0142</div>
      </div>
      <div class="col col--ca">
        <div>2190 Fraser Ridge St.</div>
        <div>Burnaby, BC V5J 2K4</div>
        <div>Canada</div>
        <div class="phone"><svg viewBox="0 0 24 24"><path d="M6.6 10.8a15.1 15.1 0 0 0 6.6 6.6l2.2-2.2a1 1 0 0 1 1-.25 11.4 11.4 0 0 0 3.6.57 1 1 0 0 1 1 1V20a1 1 0 0 1-1 1A17 17 0 0 1 3 4a1 1 0 0 1 1-1h3.5a1 1 0 0 1 1 1c0 1.25.2 2.45.57 3.57a1 1 0 0 1-.25 1z"/></svg>604-555-0178</div>
      </div>
    </div>
  </section>
</main>
</body>
</html>
```